Hong Kong based International Remittance and ForEx company requires website design

We need a website designed for a new European - Hong Kong based ForEx & fund remittence entity.

The company specialises in larger corporate & high net worth private client trades, therefore the design must aesthetically reflect this (sophisticated). As a theme colour, financial entities tend to use either blue or red; if blue, our preference is a darker blue. Visually, our preference is less copy, more imagery.

Number of pages would be limited; landing (home), about us, client registration (x1 Corporate form, x1 Private Client form), Contact Us.

Have uploaded the existing logo - please note this is to be redesigned, although the colour scheme will remain the same. Please also note that copy will follow - please use Lorem Ipsum.

Target Market(s)

Medium to large Corporations. High net worth individuals.

Industry/Entity Type

Financial Service

Coding

Coded - Design and coding required

Number of Pages Required

4 page

Font styles to use
Serif

Requirements
Nice to have
• ForEx ticker,

```html
<!DOCTYPE html>
<html lang="en">
<head>
<meta charset="utf-8">
<title>Harbourline Incorporation Limited</title>
<link rel="stylesheet" href="https://fonts.googleapis.com/css2?family=Cardo:wght@400;700&family=Cinzel:wght@400&family=Raleway:wght@400;500;600;700&display=swap">
<style>
:root{
  --navy:#0c2d62;
  --navy-deep:#0b3577;
  --ticker:#3b8fe2;
  --ink:#222;
  --muted:#555;
  --charcoal:#2c2c2f;
  --footer:#232325;
  --panel:#efefef;
  --white:#fff;
  --line:#3f3f42;
}
*{box-sizing:border-box;margin:0;padding:0}
html,body{width:1200px;height:2550px;overflow:hidden}
body{font-family:'Raleway',sans-serif;color:var(--ink);background:var(--white);position:relative}
.abs{position:absolute}
.serif{font-family:'Cardo',serif}

/* header */
.topline{position:absolute;left:0;top:0;width:1200px;height:5px;background:var(--navy)}
.header{position:absolute;left:0;top:5px;width:1200px;height:127px;background:var(--white)}
.brand{position:absolute;left:98px;top:50px;font-family:'Cardo',serif;font-size:38px;color:var(--ink);display:flex;align-items:center;gap:12px}
.brand .dot{width:14px;height:14px;border-radius:50%;background:var(--navy)}
.nav{position:absolute;left:488px;top:48px;display:flex;align-items:center;font-size:15px;font-weight:500;color:var(--ink)}
.nav a{text-decoration:none;color:inherit;margin-right:48px;padding:8px 0}
.nav a.active{border:1.5px solid #333;border-radius:20px;padding:7px 16px;margin-right:40px}
.nav a:last-child{margin-right:0}

/* ticker */
.ticker{position:absolute;left:0;top:132px;width:1200px;height:43px;background:var(--ticker);display:flex;align-items:center;color:var(--white);font-size:14px}
.ticker .label{width:213px;height:43px;background:var(--navy-deep);display:flex;align-items:center;padding-left:115px;font-weight:700;font-size:13px;border-right:4px solid #fff}
.ticker .item{margin-left:14px;width:246px}

/* hero */
.hero{position:absolute;left:0;top:175px;width:1200px;height:525px;background:linear-gradient(90deg,#141b2a 0%,#2a3446 35%,#1a2231 62%,#0f1a24 100%)}
.hero .photo{position:absolute;inset:0;background:radial-gradient(ellipse at 80% 45%,rgba(60,110,70,.35),transparent 55%),radial-gradient(ellipse at 35% 50%,rgba(120,100,90,.35),transparent 50%)}
.hero h1{position:absolute;left:0;width:1200px;top:190px;text-align:center;font-family:'Cinzel',serif;font-weight:400;font-size:40px;color:var(--white);letter-spacing:.5px}
.hero p{position:absolute;left:0;width:1200px;top:265px;text-align:center;font-size:21px;font-weight:500;line-height:39px;color:var(--white)}
.btn-ghost{position:absolute;left:540px;top:376px;width:120px;height:38px;border:1.5px solid #fff;border-radius:20px;color:#fff;font-size:14px;display:flex;align-items:center;justify-content:center}
.hero svg.arrow{position:absolute;top:232px}

/* dividers */
.divider{position:absolute;left:572px;width:56px;height:56px;border-radius:50%;background:var(--white);z-index:3}

/* section headings */
.heading{position:absolute;left:0;width:1200px;text-align:center;font-family:'Cardo',serif;font-size:31px}
.heading span.u{display:inline-block;border-bottom:1.5px solid #999;padding-bottom:2px}
.heading .blue{color:var(--navy)}
.sub{position:absolute;left:0;width:1200px;text-align:center;font-size:13.5px}

/* about */
.about p.body{position:absolute;left:140px;width:920px;text-align:center;font-size:13.5px;line-height:25px;color:var(--muted)}
.pill{position:absolute;height:38px;width:120px;border-radius:20px;color:#fff;font-size:14px;display:flex;align-items:center;justify-content:center}

/* services */
.services{position:absolute;left:0;top:1068px;width:1200px;height:542px;background:linear-gradient(180deg,#333336 0%,#262629 100%)}
.services .bg{position:absolute;inset:0;background:linear-gradient(90deg,rgba(255,255,255,.04),rgba(255,255,255,0) 30%,rgba(255,255,255,.05) 70%,rgba(255,255,255,0))}
.card{position:absolute;top:170px;width:290px;height:244px;background:var(--white);padding:6px}
.card .img{width:278px;height:188px}
.card .cap{font-size:15px;font-weight:600;margin-top:16px;padding-left:2px}
.card.feature{background:var(--white)}
.card.feature .img{height:232px;background:linear-gradient(160deg,#2f5b93,#1d3f73);color:#fff;text-align:center;padding-top:28px}
.card.feature h3{font-size:20px;font-weight:600;display:inline-block;padding-bottom:10px;border-bottom:1px solid rgba(255,255,255,.7);width:170px}
.card.feature p{font-size:13px;line-height:22px;margin:20px auto 0;width:245px}
.card.feature .mini{margin:16px auto 0;width:102px;height:34px;border:1.5px solid #fff;border-radius:18px;display:flex;align-items:center;justify-content:center;font-size:13px}
.dots{position:absolute;top:466px;left:540px;display:flex;gap:16px}
.dots i{width:8px;height:8px;border-radius:50%;background:#888;display:block}
.dots i.on{background:var(--ticker);width:10px;height:10px;margin-top:-1px}

/* blog */
.blog{position:absolute;left:0;top:1610px;width:1200px;height:508px;background:var(--panel)}
.post{position:absolute;top:100px;width:302px;height:343px;background:var(--white);border:1px solid #ddd;padding:10px}
.post .img{width:280px;height:155px}
.post h4{font-size:15.5px;font-weight:700;margin:22px 0 0 2px}
.post p{font-size:12.5px;line-height:20px;color:var(--muted);margin:12px 2px 0}
.post .btn{position:absolute;left:13px;top:290px;width:102px;height:36px;color:#fff;font-size:13px;display:flex;align-items:center;justify-content:center}

/* footer */
.footer{position:absolute;left:0;top:2118px;width:1200px;height:370px;background:var(--footer);color:#ddd}
.footer .col-title{position:absolute;top:68px;font-size:19px;font-weight:500;color:#fff}
.footer .vr{position:absolute;top:62px;width:1px;height:250px;background:var(--line)}
.fbrand{position:absolute;left:99px;top:85px;font-family:'Cardo',serif;font-size:36px;color:#fff;display:flex;align-items:center;gap:10px}
.fbrand .dot{width:12px;height:12px;border-radius:50%;background:#fff}
.finfo{position:absolute;left:99px;font-size:13.5px;line-height:30px}
.finfo .row{display:flex;gap:16px}
.finfo svg{margin-top:9px;flex:none}
.recent{position:absolute;left:386px;display:flex;gap:14px}
.recent .thumb{width:52px;height:44px}
.recent h5{font-size:12.5px;font-weight:700;color:#fff;margin-top:2px}
.recent small{display:flex;align-items:center;gap:8px;font-size:10px;margin-top:12px;color:#ccc}
.links{position:absolute;left:671px;top:112px;font-size:13.5px;line-height:31px}
.field{position:absolute;left:882px;width:220px;height:38px;background:#454548;border-radius:5px;font-size:13px;color:#ddd;padding:10px 14px}
.send{position:absolute;left:882px;top:292px;width:220px;height:38px;background:#0f5dbf;border-radius:4px;color:#fff;font-size:14px;display:flex;align-items:center;justify-content:center}
.bottom{position:absolute;left:0;top:2488px;width:1200px;height:62px;background:linear-gradient(90deg,#0b3272,#1257a8 70%,#0b3272);color:#fff;font-size:12.5px}
.bottom .copy{position:absolute;left:99px;top:23px}
.social{position:absolute;left:873px;top:14px;display:flex;gap:12px;align-items:center}
.social i{display:block;width:30px;height:30px;border:1.5px solid #fff;border-radius:50%}
.social .badge{width:34px;height:34px;border:none;border-radius:50%;background:#c8a13a;margin-right:14px}
</style>
</head>
<body>

<div class="topline"></div>
<header class="header">
  <div class="brand"><span class="dot"></span>Harbourline</div>
  <nav class="nav">
    <a class="active">Home</a><a>About US</a><a>Our Services</a><a>BLog Post</a><a>Contact Us</a>
  </nav>
</header>

<div class="ticker">
  <div class="label">Forex Ticker</div>
  <div class="item">&gt; British Pound Sterling &nbsp;- 100</div>
  <div class="item">&gt; Hong Kong Dollar &nbsp;- 1078.41</div>
  <div class="item">&gt; Bolivian Boliviano &nbsp;- 2015.20</div>
  <div class="item">Algerian Dinar &nbsp;- 21.2</div>
</div>

<section class="hero">
  <div class="photo" role="img" aria-label="Trader at a desk studying currency rates on a monitor"></div>
  <h1>HARBOURLINE INCORPORATION LIMITED</h1>
  <p>We are a new ForEx &amp; fund remittance entity<br>based in European - Hong Kong.</p>
  <div class="btn-ghost">Read More</div>
  <svg class="arrow" style="left:22px" width="32" height="60" viewBox="0 0 32 60"><polyline points="28,2 4,30 28,58" fill="none" stroke="#fff" stroke-width="1.5"/></svg>
  <svg class="arrow" style="left:1146px" width="32" height="60" viewBox="0 0 32 60"><polyline points="4,2 28,30 4,58" fill="none" stroke="#fff" stroke-width="1.5"/></svg>
</section>

<div class="divider" style="top:672px"></div>

<section class="about">
  <div class="heading" style="top:722px"><span class="u">About <span class="blue">Harbourline Incorporation</span></span></div>
  <div class="sub" style="top:776px;color:var(--muted)">Harbourline is a leading provider of international payment services</div>
  <p class="body" style="top:818px">Harbourline is a leading provider of international payment services and foreign exchange to corporations and individuals covering most of the world including; &nbsp;throughout Asia, South America, and Europe. We engage with our clients with unmatched personalised service and aim to establish longevity with all our client relationships.</p>
  <p class="body" style="top:902px">Coupled with our excellent customer service, highly competitive rates and in depth market knowledge we provide a simple, reliable and cost effective service to all of our clients.</p>
  <div class="pill" style="left:473px;top:977px;background:var(--navy)">Read More</div>
  <div class="pill" style="left:610px;top:977px;background:#3a3a3c">Contact Us</div>
</section>

<div class="divider" style="top:1040px"></div>

<section class="services">
  <div class="bg" role="img" aria-label="Dark city skyline of office towers"></div>
  <div class="heading" style="top:48px;color:#fff"><span class="u" style="border-color:#aaa">Our Services</span></div>
  <div class="sub" style="top:104px;color:#ddd">Our expertise service areas</div>
  <div class="card" style="left:99px">
    <div class="img" role="img" aria-label="Stack of coins on banknotes" style="background:linear-gradient(160deg,#c9b7a3,#8f8472 55%,#d9c9c2)"></div>
    <div class="cap">International Money Transfer</div>
  </div>
  <div class="card feature" style="left:455px">
    <div class="img" role="img" aria-label="Business meeting shaded in blue">
      <h3>Foreign Exchange</h3>
      <p>We provide the international settlement and reconciliation of funds for and on behalf of our clients</p>
      <div class="mini">Read More</div>
    </div>
  </div>
  <div class="card" style="left:812px">
    <div class="img" role="img" aria-label="Two business people shaking hands" style="background:linear-gradient(135deg,#e9e6e3,#c8b3a0 50%,#3a3b40)"></div>
    <div class="cap">Paying &amp; Receiving Agency</div>
  </div>
  <div class="dots"><i></i><i></i><i class="on"></i><i></i><i></i></div>
</section>

<div class="divider" style="top:1582px"></div>

<section class="blog">
  <div class="heading" style="top:36px"><span class="u"><span style="color:var(--ink)">Harbourline</span> <span class="blue">Blog</span></span></div>
  <article class="post" style="left:99px">
    <div class="img" role="img" aria-label="Group of business people in an office" style="background:linear-gradient(180deg,#e8eaec,#6c6a6a)"></div>
    <h4>Neque porro quisquam dolorem</h4>
    <p>Nemo enim ipsam voluptatem quia voluptas sit aspernatur aut odit aut fugit, sed quia conse quuntur magni dolores eosqui</p>
    <div class="btn" style="background:var(--navy)">Read More</div>
  </article>
  <article class="post" style="left:449px">
    <div class="img" role="img" aria-label="Businesswoman working at a laptop" style="background:linear-gradient(180deg,#eef0f2,#9a9693)"></div>
    <h4>Neque porro quisquam dolorem</h4>
    <p>Nemo enim ipsam voluptatem quia voluptas sit aspernatur aut odit aut fugit, sed quia conse quuntur magni dolores eosqui</p>
    <div class="btn" style="background:#3a3a3c">Read More</div>
  </article>
  <article class="post" style="left:798px">
    <div class="img" role="img" aria-label="Students reading together" style="background:linear-gradient(135deg,#f0ece6,#a27b62 55%,#7a4a8c)"></div>
    <h4>Neque porro quisquam dolorem</h4>
    <p>Nemo enim ipsam voluptatem quia voluptas sit aspernatur aut odit aut fugit, sed quia conse quuntur magni dolores eosqui</p>
    <div class="btn" style="background:#3a3a3c">Read More</div>
  </article>
</section>

<div class="divider" style="top:2090px"></div>

<footer class="footer">
  <div class="fbrand"><span class="dot"></span>Harbourline</div>
  <div class="finfo" style="top:170px">
    <div class="row">
      <svg width="12" height="14" viewBox="0 0 12 16"><path d="M6 0a6 6 0 0 0-6 6c0 4.5 6 10 6 10s6-5.5 6-10a6 6 0 0 0-6-6zm0 8.5A2.5 2.5 0 1 1 6 3.5a2.5 2.5 0 0 1 0 5z" fill="#fff"/></svg>
      <div>Meadow House Elmbrook Lane<br>Elmbrook Road EN4 2QT</div>
    </div>
    <div class="row">
      <svg width="13" height="10" viewBox="0 0 14 10"><rect width="14" height="10" rx="1" fill="#fff"/><polyline points="0,0 7,6 14,0" fill="none" stroke="#232325" stroke-width="1.4"/></svg>
      <div style="line-height:22px;padding-top:4px">Email: &nbsp;info@harbourline<br>incorporation.com</div>
    </div>
    <div class="row" style="margin-top:6px">
      <svg width="13" height="13" viewBox="0 0 14 14"><rect width="14" height="14" rx="2" fill="#fff"/><path d="M4 3l2 2-1 1.5c.6 1.3 1.4 2.1 2.6 2.6L9 8l2 2-1.3 1.5C6 11 3 8 2.6 4.3z" fill="#232325"/></svg>
      <div>Phone: (852) 2190 4518</div>
    </div>
  </div>

  <div class="vr" style="left:353px"></div>
  <div class="col-title" style="left:386px">Recent Posts</div>
  <div class="recent" style="top:116px"><div class="thumb" role="img" aria-label="Post thumbnail" style="background:linear-gradient(135deg,#bba08a,#5b4a44)"></div><div><h5>Planning For The Future</h5><small><svg width="9" height="9" viewBox="0 0 10 10"><rect width="10" height="10" fill="#ccc"/></svg>NOV 12, 2015</small></div></div>
  <div class="recent" style="top:183px"><div class="thumb" role="img" aria-label="Post thumbnail" style="background:linear-gradient(135deg,#d9d2c8,#7e92a6)"></div><div><h5>Planning For The Future</h5><small><svg width="9" height="9" viewBox="0 0 10 10"><rect width="10" height="10" fill="#ccc"/></svg>NOV 12, 2015</small></div></div>
  <div class="recent" style="top:250px"><div class="thumb" role="img" aria-label="Post thumbnail" style="background:linear-gradient(135deg,#6aa0a6,#3d4e58)"></div><div><h5>Planning For The Future</h5><small><svg width="9" height="9" viewBox="0 0 10 10"><rect width="10" height="10" fill="#ccc"/></svg>NOV 12, 2015</small></div></div>

  <div class="vr" style="left:635px"></div>
  <div class="col-title" style="left:671px">Additional Links</div>
  <div class="links">&gt;&gt; Home<br>&gt;&gt; About US<br>&gt;&gt; Services<br>&gt;&gt; Client Registration<br>&gt;&gt; Contact Us</div>

  <div class="vr" style="left:849px"></div>
  <div class="col-title" style="left:882px">Contact Us</div>
  <div class="field" style="top:114px">Name</div>
  <div class="field" style="top:165px">Email Address</div>
  <div class="field" style="top:216px;height:64px">Comments</div>
  <div class="send">Contact Us</div>
</footer>

<div class="bottom">
  <div class="copy">© 2016 Harbourline Incorporation Limited. All Rights Reserved</div>
  <div class="social"><i class="badge"></i><i></i><i></i><i></i><i></i></div>
</div>

</body>
</html>
```